Coastline Premier Retreats Business Card Design

Design a business card for Coastline Premier Retreats. Look at the website for colors and reference. Card should have logo, name, title, office number, mobile number, email, URL and a tagline like, "Luxury Hotel & Resort Email Marketing" (This might change).

https://www.coastlinepremierretreats.example

The rest I will leave up to your imagination.

Contact Information for Business Card

Logo, name, title, office number, mobile number, email, URL and a tagline like, "Luxury Hotel & Resort Email Marketing" (This might change).

```html
<!DOCTYPE html>
<html lang="en">
<head>
<meta charset="utf-8">
<title>Coastline Premier Retreats – Business Card</title>
<link href="https://fonts.googleapis.com/css2?family=Open+Sans:wght@400;600;700&display=swap" rel="stylesheet">
<style>
  :root {
    --backdrop: #232323;
    --card: #1f1f22;
    --card-glow: #28282c;
    --orange: #f47a20;
    --white: #ffffff;
    --muted: #e6e6e6;
  }
  * { box-sizing: border-box; margin: 0; padding: 0; }
  html, body {
    width: 1200px; height: 780px; overflow: hidden;
    background: var(--backdrop);
    font-family: "Open Sans", Arial, sans-serif;
  }
  .canvas {
    position: relative; width: 1200px; height: 780px;
    display: flex; align-items: center; justify-content: center; gap: 50px;
  }
  .card {
    position: relative; width: 525px; height: 300px;
    background: var(--card); overflow: hidden;
    box-shadow: 0 18px 40px rgba(0,0,0,.45);
  }
  .card__curve { position: absolute; inset: 0; }

  /* wordmark */
  .wordmark {
    position: absolute; display: flex; align-items: center; gap: 10px;
    color: var(--white); font-weight: 700; text-transform: uppercase;
    letter-spacing: .04em; line-height: 1.1;
  }
  .wordmark__square { width: 12px; height: 12px; background: var(--orange); flex: none; }
  .card--front .wordmark { top: 30px; left: 30px; font-size: 17px; }
  .card--back .wordmark {
    top: 50%; left: 50%; transform: translate(-50%, -50%);
    font-size: 26px; white-space: nowrap; gap: 14px;
  }
  .card--back .wordmark__square { width: 16px; height: 16px; }

  /* identity */
  .identity { position: absolute; top: 92px; right: 40px; text-align: right; }
  .identity__name { font-size: 27px; font-weight: 700; color: var(--white); line-height: 1.1; }
  .identity__first { color: var(--orange); }
  .identity__title { font-size: 13px; color: var(--white); margin-top: 2px; }
  .card__tab {
    position: absolute; right: 0; top: 112px; width: 14px; height: 40px;
    background: var(--orange);
  }
  .tagline {
    position: absolute; top: 168px; right: 40px; text-align: right;
    color: var(--orange); font-size: 13px; line-height: 1.35;
  }

  /* contact */
  .contact {
    position: absolute; right: 20px; bottom: 16px; list-style: none;
    text-align: right; color: var(--muted); font-size: 11.5px; line-height: 1.6;
  }
  .contact__item { display: flex; align-items: center; justify-content: flex-end; gap: 8px; }
  .contact__icon { width: 12px; height: 12px; flex: none; }
</style>
</head>
<body>
<main class="canvas">

  <section class="card card--front" aria-label="Business card front">
    <svg class="card__curve" viewBox="0 0 525 300" preserveAspectRatio="none" aria-hidden="true">
      <defs>
        <radialGradient id="curveShade" cx="0.6" cy="0.65" r="0.6">
          <stop offset="0" stop-color="#1d1d20"/>
          <stop offset="1" stop-color="#26262a"/>
        </radialGradient>
      </defs>
      <path d="M110 300 C 130 170, 230 90, 380 85 L 525 85 L 525 300 Z" fill="url(#curveShade)"/>
    </svg>

    <div class="wordmark"><span class="wordmark__square"></span><span>Coastline<br>Premier Retreats</span></div>

    <div class="identity">
      <p class="identity__name"><span class="identity__first">Lenka</span> Marovic</p>
      <p class="identity__title">Managing Director</p>
    </div>
    <span class="card__tab"></span>

    <p class="tagline">Luxury Hotel &amp;<br>Resort Email Marketing</p>

    <ul class="contact">
      <li class="contact__item">(555) 014-2758
        <svg class="contact__icon" viewBox="0 0 12 12" aria-hidden="true"><path d="M2.5 1 L4.5 1 L5.2 3.6 L4 4.5 C4.6 5.9 6 7.3 7.5 8 L8.4 6.8 L11 7.5 L11 9.5 C11 10.3 10.3 11 9.5 11 C5 11 1 7 1 2.5 C1 1.7 1.7 1 2.5 1 Z" fill="var(--orange)"/></svg>
      </li>
      <li class="contact__item">(555) 014-7777
        <svg class="contact__icon" viewBox="0 0 12 12" aria-hidden="true"><rect x="3" y="0.8" width="6" height="10.4" rx="1" fill="none" stroke="var(--orange)" stroke-width="1.2"/><circle cx="6" cy="9.4" r=".6" fill="var(--orange)"/></svg>
      </li>
      <li class="contact__item">www.coastlinepremierretreats.example
        <svg class="contact__icon" viewBox="0 0 12 12" aria-hidden="true"><circle cx="6" cy="6" r="5" fill="none" stroke="var(--orange)" stroke-width="1.2"/><ellipse cx="6" cy="6" rx="2.2" ry="5" fill="none" stroke="var(--orange)" stroke-width="1"/><path d="M1 6 H11" stroke="var(--orange)" stroke-width="1"/></svg>
      </li>
      <li class="contact__item">info@coastlinepremierretreats.example
        <svg class="contact__icon" viewBox="0 0 12 12" aria-hidden="true"><rect x="1" y="2.5" width="10" height="7" fill="var(--orange)"/><path d="M1 2.5 L6 6.5 L11 2.5" fill="none" stroke="var(--card)" stroke-width="1"/></svg>
      </li>
    </ul>
  </section>

  <section class="card card--back" aria-label="Business card back">
    <div class="wordmark"><span class="wordmark__square"></span><span>Coastline Premier Retreats</span></div>
  </section>

</main>
</body>
</html>
```